Hartwell Estates Business Cards

I would like a business card that includes myself and my partner.
Includes: Logo, office #, email, website, our names, our numbers and possibly the address. I would also like the logo to be embossed and the card to be horizontal.
There is a photo of our yard signs to give you an idea of the colors of our business.

Target Market(s)

Everyone in real estate market.
We are in a rural area. Our clientele are from all socioeconomic backgrounds.

Industry/Entity Type

Real Estate Agent

Contact Information for Business Card

Company Name: Hartwell Estates
Our Names, Titles & Cell #'s : Dana Pembrook-Broker (555).317.6624, Marla Pembrook-Realtor (555).609.1385
Office #: (555).240.3918
Website: hartwellestates-demo.com
Joint Email: pembrook@hartwellestates-demo.com
Office Address: 418B W. Calloway Ave.
Alder Glen, QX. 70913

Font styles to use
Serif

Requirements
Must have
• HORIZONTAL, Logo, Myself and my partners names, Our cell #'s, our office #, our website, our email address
Nice to have
• Embossed logo, office address, our titles.

```html
<!DOCTYPE html>
<html lang="en">
<head>
<meta charset="utf-8">
<title>Hartwell Estates Business Cards</title>
<link rel="stylesheet" href="https://fonts.googleapis.com/css2?family=Open+Sans:wght@400;600;700&display=swap">
<style>
  :root {
    --purple: #4a1f66;
    --ink: #3a3a3a;
    --band-dark: #1f1f1f;
    --card: #ffffff;
    --backdrop: #e9e6e2;
  }
  * { margin: 0; padding: 0; box-sizing: border-box; }
  html, body { width: 1200px; height: 900px; overflow: hidden; }
  body {
    background: var(--backdrop);
    font-family: "Open Sans", Arial, sans-serif;
    position: relative;
  }
  .card {
    position: absolute;
    left: 285px;
    width: 630px;
    height: 360px;
    background: var(--card);
    box-shadow: 0 6px 18px rgba(0,0,0,0.15);
    overflow: hidden;
  }
  .card--front { top: 50px; }
  .card--back { top: 470px; }

  /* Front */
  .front-mark {
    position: absolute;
    inset: 0;
    display: flex;
    align-items: center;
    justify-content: center;
    gap: 18px;
  }
  .front-mark__dot {
    width: 46px; height: 46px;
    border-radius: 50%;
    background: var(--purple);
  }
  .front-mark__name {
    color: var(--purple);
    font-weight: 700;
    font-size: 44px;
    letter-spacing: 0.5px;
  }

  /* Back */
  .contact {
    position: absolute;
    left: 44px;
    top: 28px;
    color: var(--ink);
    font-size: 13.5px;
    line-height: 1.35;
  }
  .person { margin-bottom: 8px; }
  .person__name {
    color: var(--purple);
    font-weight: 700;
    font-size: 17px;
    line-height: 1.2;
  }
  .person__title { font-size: 12.5px; }
  .line { display: flex; align-items: center; gap: 8px; white-space: nowrap; }
  .line svg { width: 12px; height: 12px; flex: none; fill: var(--purple); }
  .office { margin-top: 4px; }
  .office__address { margin-bottom: 6px; }

  .back-mark {
    position: absolute;
    right: 40px;
    top: 128px;
    color: var(--purple);
    font-weight: 700;
    font-size: 30px;
    text-align: center;
    line-height: 1.1;
  }
  .bands { position: absolute; left: 0; bottom: 0; width: 630px; height: 60px; }
</style>
</head>
<body>

<section class="card card--front" aria-label="Card front">
  <div class="front-mark">
    <span class="front-mark__dot"></span>
    <span class="front-mark__name">Hartwell Estates</span>
  </div>
</section>

<section class="card card--back" aria-label="Card back">
  <div class="contact">
    <div class="person">
      <div class="person__name">Dana Pembrook</div>
      <div class="person__title">Broker</div>
      <div class="line">
        <svg viewBox="0 0 24 24"><path d="M6.6 10.8a15 15 0 0 0 6.6 6.6l2.2-2.2a1 1 0 0 1 1-.25 11.4 11.4 0 0 0 3.6.57 1 1 0 0 1 1 1V20a1 1 0 0 1-1 1A17 17 0 0 1 3 4a1 1 0 0 1 1-1h3.5a1 1 0 0 1 1 1c0 1.25.2 2.45.57 3.57a1 1 0 0 1-.25 1z"/></svg>
        (555).317.6624
      </div>
    </div>
    <div class="person">
      <div class="person__name">Marla Pembrook</div>
      <div class="person__title">Realtor</div>
      <div class="line">
        <svg viewBox="0 0 24 24"><path d="M6.6 10.8a15 15 0 0 0 6.6 6.6l2.2-2.2a1 1 0 0 1 1-.25 11.4 11.4 0 0 0 3.6.57 1 1 0 0 1 1 1V20a1 1 0 0 1-1 1A17 17 0 0 1 3 4a1 1 0 0 1 1-1h3.5a1 1 0 0 1 1 1c0 1.25.2 2.45.57 3.57a1 1 0 0 1-.25 1z"/></svg>
        (555).609.1385
      </div>
    </div>
    <div class="office">
      <div class="office__address">418B W. Calloway Ave.<br>Alder Glen, QX. 70913</div>
      <div class="line">
        <svg viewBox="0 0 24 24"><path d="M6.6 10.8a15 15 0 0 0 6.6 6.6l2.2-2.2a1 1 0 0 1 1-.25 11.4 11.4 0 0 0 3.6.57 1 1 0 0 1 1 1V20a1 1 0 0 1-1 1A17 17 0 0 1 3 4a1 1 0 0 1 1-1h3.5a1 1 0 0 1 1 1c0 1.25.2 2.45.57 3.57a1 1 0 0 1-.25 1z"/></svg>
        (555).240.3918
      </div>
      <div class="line">
        <svg viewBox="0 0 24 24"><path d="M2 5h20v14H2z M2 5l10 8 10-8" fill="none" stroke="#4a1f66" stroke-width="2.5"/></svg>
        pembrook@hartwellestates-demo.com
      </div>
      <div class="line">
        <svg viewBox="0 0 24 24"><circle cx="12" cy="12" r="9" fill="none" stroke="#4a1f66" stroke-width="2.5"/><path d="M3 12h18M12 3c3 3 3 15 0 18M12 3c-3 3-3 15 0 18" fill="none" stroke="#4a1f66" stroke-width="1.8"/></svg>
        hartwellestates-demo.com
      </div>
    </div>
  </div>

  <div class="back-mark">Hartwell<br>Estates</div>

  <svg class="bands" viewBox="0 0 630 60" aria-hidden="true">
    <polygon points="0,30 250,30 240,46 0,46" fill="var(--band-dark)"/>
    <polygon points="262,26 630,26 630,60 238,60" fill="var(--purple)"/>
  </svg>
</section>

</body>
</html>
```